Business Card Design Project

Basic business card with minimal details. I just need company name, email & web address, telephone and my name.
I would like the back of the card to be grey with my logo & company name centred.

Target Market(s)

Architects
Builders
Property Developers

Industry/Entity Type

Business

Font styles to use
Sans Serif

Colors

Designer to choose colors to be used in the design.

Requirements
Must have
• Tallow Crest
Rupert Hazelby - Director
M: 0427 915203
E: rupert@tallowcrest.com.au
W: www.tallowcrest.com.au
Should not have
• No other images or pictures

```html
<!DOCTYPE html>
<html lang="en">
<head>
<meta charset="utf-8">
<title>Tallow Crest – Business Card</title>
<link rel="stylesheet" href="https://fonts.googleapis.com/css2?family=Exo+2:wght@400;500;600&display=swap">
<style>
  :root {
    --backdrop: #2e2924;
    --card-white: #ffffff;
    --brand-red: #d42a4c;
    --band-red-dark: #b31e3a;
    --band-red-light: #e83e64;
    --slate-dark: #4d6171;
    --slate-light: #8ca9bc;
    --wordmark: #627d8f;
    --text-light: #ffffff;
  }
  html, body {
    margin: 0;
    width: 1200px;
    height: 900px;
    overflow: hidden;
    background: var(--backdrop);
  }
  .card {
    position: absolute;
    left: 65px;
    top: 143px;
    width: 1070px;
    height: 614px;
    border-radius: 28px;
    overflow: hidden;
    background: var(--card-white);
    font-family: "Exo 2", sans-serif;
  }
  .brand {
    position: absolute;
    left: 86px;
    top: 100px;
    display: flex;
    align-items: center;
    gap: 34px;
  }
  .brand-square {
    width: 62px;
    height: 62px;
    background: var(--brand-red);
  }
  .brand-name {
    margin: 0;
    font-size: 72px;
    font-weight: 500;
    letter-spacing: 4px;
    color: var(--wordmark);
    text-transform: uppercase;
    line-height: 1;
  }
  .accent-band {
    position: absolute;
    left: 0;
    top: 288px;
    width: 100%;
    height: 32px;
    background: linear-gradient(90deg, var(--band-red-dark) 0%, var(--band-red-light) 45%, var(--band-red-light) 60%, var(--band-red-dark) 100%);
  }
  .details-panel {
    position: absolute;
    left: 0;
    top: 320px;
    width: 100%;
    height: 294px;
    background: linear-gradient(90deg, var(--slate-dark) 0%, var(--slate-light) 38%, var(--slate-light) 55%, var(--slate-dark) 100%);
    color: var(--text-light);
  }
  .person {
    position: absolute;
    left: 70px;
    top: 42px;
  }
  .person-name {
    margin: 0;
    font-size: 35px;
    font-weight: 600;
    letter-spacing: 0.5px;
    line-height: 1;
    text-transform: uppercase;
  }
  .person-role {
    margin: 4px 0 0;
    font-size: 20px;
    font-weight: 400;
  }
  .contact-list {
    position: absolute;
    left: 70px;
    top: 148px;
    margin: 0;
    padding: 0;
    list-style: none;
  }
  .contact-item {
    display: flex;
    align-items: center;
    height: 37px;
    font-size: 26px;
    font-weight: 400;
  }
  .contact-icon {
    width: 30px;
    height: 26px;
    margin-right: 26px;
    fill: none;
    stroke: var(--text-light);
    stroke-width: 2.2;
  }
</style>
</head>
<body>
  <section class="card">
    <div class="brand">
      <div class="brand-square"></div>
      <h1 class="brand-name">Tallow Crest</h1>
    </div>

    <div class="accent-band"></div>

    <div class="details-panel">
      <div class="person">
        <h2 class="person-name">Rupert Hazelby</h2>
        <p class="person-role">Director</p>
      </div>

      <ul class="contact-list">
        <li class="contact-item">
          <svg class="contact-icon" viewBox="0 0 30 26" aria-hidden="true">
            <path d="M2 9 Q15 1 28 9 L26 12 L21 10 L21 8 Q15 6 9 8 L9 10 L4 12 Z" fill="#fff"/>
            <path d="M7 13 L23 13 L26 24 L4 24 Z" fill="#fff"/>
          </svg>
          <span>0427 915203</span>
        </li>
        <li class="contact-item">
          <svg class="contact-icon" viewBox="0 0 30 26" aria-hidden="true">
            <rect x="2" y="3" width="26" height="20"/>
            <path d="M2 3 L15 15 L28 3 M2 23 L12 12 M28 23 L18 12"/>
          </svg>
          <span>rupert@tallowcrest.com.au</span>
        </li>
        <li class="contact-item">
          <svg class="contact-icon" viewBox="0 0 30 26" aria-hidden="true">
            <rect x="2" y="2" width="26" height="16"/>
            <path d="M15 18 L15 23 M9 24 L21 24"/>
          </svg>
          <span>www.tallowcrest.com.au</span>
        </li>
      </ul>
    </div>
  </section>
</body>
</html>
```